Stationery Design for a fast food resturaunt

We just created our logo, we need nice stationary to go with it. We beed the design to be on white background and black background.

Target Market(s)

Landlords who will lease their retail shops to us. Shopping Mall Management.Real Estate Professionals.

Font styles to use
Sans Serif

```html
<!DOCTYPE html>
<html lang="en">
<head>
<meta charset="utf-8">
<title>Amber Hive – Business Cards</title>
<link href="https://fonts.googleapis.com/css2?family=Questrial&family=Montserrat:wght@600&display=swap" rel="stylesheet">
<style>
  :root {
    --backdrop: #e3e5e7;
    --charcoal: #363636;
    --amber: #f2b100;
    --paper: #ffffff;
    --ink: #3a3a3a;
    --shadow: rgba(0, 0, 0, 0.18);
  }
  * { box-sizing: border-box; margin: 0; padding: 0; }
  html, body {
    width: 1200px; height: 1000px; overflow: hidden;
    background: var(--backdrop);
    font-family: "Questrial", sans-serif;
  }
  .card {
    position: absolute;
    width: 560px; height: 320px;
    left: 320px;
    box-shadow: 0 14px 30px var(--shadow);
    overflow: hidden;
  }
  /* Back of card */
  .card--back {
    top: 110px;
    background: var(--charcoal);
    display: flex; align-items: center; justify-content: center;
  }
  .brand {
    display: flex; align-items: center; gap: 16px;
    color: var(--amber);
    font-size: 44px; letter-spacing: 6px;
    text-transform: uppercase;
  }
  .brand__mark {
    width: 22px; height: 22px; background: var(--paper);
  }
  /* Front of card */
  .card--front {
    top: 540px;
    background: var(--paper);
  }
  .card__band {
    position: absolute; left: 0; right: 0; bottom: 0;
    height: 22px; background: var(--charcoal);
    border-top: 5px solid var(--amber);
    box-sizing: content-box;
  }
  .card--front .brand {
    position: absolute; left: 42px; top: 48px;
    font-size: 32px; letter-spacing: 5px; gap: 12px;
  }
  .card--front .brand__mark {
    width: 18px; height: 18px; background: var(--charcoal);
  }
  .contact {
    position: absolute; left: 300px; top: 118px;
    color: var(--ink); font-size: 15px; line-height: 1.5;
  }
  .contact__name {
    font-family: "Montserrat", sans-serif; font-weight: 600;
    color: var(--amber); font-size: 17px; letter-spacing: 1px;
    text-transform: uppercase;
  }
  .contact__role { margin-bottom: 6px; }
  .contact__line { display: flex; align-items: center; gap: 8px; }
  .contact__icon { width: 15px; height: 15px; flex: none; }
  .contact__address { margin-top: 4px; }
</style>
</head>
<body>

<section class="card card--back">
  <div class="brand"><span class="brand__mark"></span>Amber Hive</div>
</section>

<section class="card card--front">
  <div class="brand"><span class="brand__mark"></span>Amber Hive</div>

  <div class="contact">
    <p class="contact__name">Sam Porter</p>
    <p class="contact__role">Managing Director</p>
    <p class="contact__line">
      <svg class="contact__icon" viewBox="0 0 16 16" aria-hidden="true">
        <rect width="16" height="16" fill="var(--amber)"/>
        <path d="M5 3.5l2 2-1 1.2c.6 1.4 1.6 2.4 3 3l1.2-1 2 2-1.3 1.5C7.5 12 4 8.5 3.8 5z" fill="#fff"/>
      </svg>
      +61 800-555-0192
    </p>
    <p class="contact__line">
      <svg class="contact__icon" viewBox="0 0 16 16" aria-hidden="true">
        <rect width="16" height="16" fill="var(--amber)"/>
        <rect x="3" y="4.5" width="10" height="7" fill="none" stroke="#fff" stroke-width="1.3"/>
        <path d="M3 4.5l5 4 5-4" fill="none" stroke="#fff" stroke-width="1.3"/>
      </svg>
      info@amberhive.com
    </p>
    <p class="contact__line">
      <svg class="contact__icon" viewBox="0 0 16 16" aria-hidden="true">
        <rect width="16" height="16" fill="var(--amber)"/>
        <circle cx="8" cy="8" r="4.8" fill="none" stroke="#fff" stroke-width="1.2"/>
        <path d="M3.2 8h9.6M8 3.2c-2.4 2.6-2.4 7 0 9.6M8 3.2c2.4 2.6 2.4 7 0 9.6" fill="none" stroke="#fff" stroke-width="1"/>
      </svg>
      www.amberhive.com
    </p>
    <p class="contact__address">18 Maple Court<br>Lake Vista, CA 90000</p>
  </div>

  <div class="card__band"></div>
</section>

</body>
</html>
```